Corporate Template

Looking for a set of corporate slides to be made which contain multiple different slides and orientations. Looking for at least 8 to 10 different master pages plus a Coversheet and closeout page. Incorporating a color palate similar to our logo coloring is preferred.
I have attached a logo.
I like the amber quill works designs best so far. They seem to fit what I'm looking for in terms of visual appearance.
Reason: I'm trying to allow time for a couple new designers to incorporate some changes I requested to their existing designs.

```html
<!DOCTYPE html>
<html lang="en">
<head>
<meta charset="utf-8">
<title>Corporate Slide Template</title>
<link href="https://fonts.googleapis.com/css2?family=Roboto:wght@300;400;500;700&display=swap" rel="stylesheet">
<style>
  :root{
    --sheet:#e6e6e6;
    --white:#ffffff;
    --cyan:#3fc0ec;
    --aqua:#7ff1fb;
    --blue:#0f97e8;
    --blue-deep:#1a62c2;
    --brand:#1c5fb8;
    --navy:#0d3a7d;
    --ink:#4a4a4a;
    --muted:#a3a3a3;
    --placeholder:#d4d4d4;
    --series-1:#0d4f91;
    --series-2:#3fc3ee;
    --series-3:#a9c66b;
    --series-4:#9b84b8;
  }
  *{margin:0;padding:0;box-sizing:border-box}
  html,body{width:784px;height:1200px;overflow:hidden;background:var(--sheet)}
  body{position:relative;font-family:"Roboto",Arial,sans-serif;color:var(--ink)}

  .slide{position:absolute;width:355px;height:267px;background:var(--white);overflow:hidden}
  .col-a{left:30px}.col-b{left:396px}
  .row-1{top:32px}.row-2{top:306px}.row-3{top:579px}.row-4{top:855px}

  .corner{position:absolute;right:0;top:0;width:48px;height:62px;background:var(--cyan);clip-path:polygon(0 0,100% 0,100% 100%)}
  .aqua-wedge{position:absolute;left:0;bottom:34px;width:50px;height:78px;background:var(--aqua);clip-path:polygon(0 0,100% 100%,0 100%)}

  .band{position:absolute;left:0;right:0;bottom:0;height:103px;
    background:linear-gradient(120deg,#0e93e6 0 18%,#1b5fc0 30%,#0d8fe4 44%,#0aa4ef 70%,#19b6f4 100%)}
  .cover-wedge{position:absolute;left:0;top:104px;width:60px;height:61px;background:var(--aqua);clip-path:polygon(0 0,100% 100%,0 100%)}

  .footer{position:absolute;left:0;right:0;bottom:0;height:34px;
    background:linear-gradient(115deg,#1b74d3 0 28%,#0b9ff0 46%,#0ab0f3 70%,#19b8f4 100%);color:var(--white)}
  .footer-text{position:absolute;top:50%;transform:translateY(-50%);font-size:6.5px;white-space:nowrap}
  .page-no{left:28px;font-weight:700}
  .deck-title{left:72px;color:rgba(255,255,255,.55);letter-spacing:.3px}
  .deck-sub{left:177px;font-weight:700}

  .mark{position:absolute;font-weight:700;line-height:1;text-align:center;white-space:nowrap}
  .mark .name{display:block}
  .mark .sub{display:block;letter-spacing:.2px}
  .mark-cover{left:0;width:355px;top:112px;color:var(--brand)}
  .mark-cover .name{font-size:31px;letter-spacing:.5px}
  .mark-cover .sub{font-size:11px;margin-top:4px}
  .mark-small{right:10px;bottom:9px;color:var(--white)}
  .mark-small .name{font-size:10px}
  .mark-small .sub{font-size:4px;margin-top:1px}
  .footer .mark-small{bottom:auto;top:50%;transform:translateY(-50%)}

  .title-block{position:absolute;left:0;width:250px;top:58px;text-align:center}
  .title-block .kicker{font-size:10px;color:var(--cyan);letter-spacing:.2px}
  .title-block h1{font-size:22px;font-weight:700;color:var(--brand);line-height:1.05;margin-top:2px}
  .title-block h2{font-size:12px;font-weight:700;color:var(--navy)}

  .agenda-rail{position:absolute;right:0;top:0;width:48px;bottom:34px;background:var(--aqua)}
  .agenda-rail::after{content:"";position:absolute;inset:0;background:var(--cyan);clip-path:polygon(0 0,100% 0,100% 45%)}
  .agenda{position:absolute;left:37px;top:33px;width:264px}
  .agenda h3{font-size:11.5px;font-weight:700;color:var(--ink);margin-bottom:6px}
  .agenda h4{font-size:7.5px;font-weight:700;color:var(--brand);margin:13px 0 3px 2px}
  .agenda h4:first-of-type{margin-top:0}
  .agenda-item{display:flex;align-items:flex-end;height:11px;font-size:7.5px;font-weight:400;color:var(--muted);padding-left:2px}
  .agenda-item::before{content:"";width:0;height:0;border-left:4px solid var(--cyan);border-top:3.5px solid transparent;border-bottom:3.5px solid transparent;margin:0 11px 1px 0}
  .agenda-item .leader{flex:1;border-bottom:1px dotted #c8c8c8;margin:0 6px 2px 3px}
  .agenda-item .ref{color:var(--brand);font-size:6.5px}

  .label{font-size:7.5px;font-weight:700;color:var(--navy)}
  .role{font-size:6.5px;color:var(--cyan)}
  .fine{font-size:5px;line-height:1.35;color:var(--muted)}

  .placeholder{position:absolute;background:var(--placeholder);display:flex;align-items:center;justify-content:center}
  .placeholder svg{display:block}

  .company-title{position:absolute;left:27px;top:22px}
  .company-intro{position:absolute;left:27px;top:50px;width:128px}
  .bullet{position:absolute;left:27px;width:140px;display:flex}
  .bullet::before{content:"";flex:none;width:0;height:0;border-left:9px solid var(--cyan);border-top:7px solid transparent;border-bottom:7px solid transparent;margin-right:12px}
  .bullet p{width:106px}

  .member{position:absolute;width:104px;text-align:center;top:0}
  .member .avatar{position:absolute;left:9px;top:35px;width:86px;height:86px;border-radius:50%}
  .member .label{position:absolute;top:139px;left:0;right:0}
  .member .role{position:absolute;top:148px;left:0;right:0}
  .member .fine{position:absolute;top:160px;left:10px;width:84px;text-align:left}

  .divider{position:absolute;left:25px;right:28px;top:120px;height:1px;background:#e9e9e9}

  .legend{position:absolute;left:194px;width:130px}
  .legend .series{display:flex;align-items:center;font-size:6.5px;color:var(--cyan)}
  .legend .series i{width:4.5px;height:4.5px;margin-right:8px}
  .legend .fine{margin-left:15px;margin-top:2px}

  .thanks{position:absolute;left:0;width:358px;top:62px;text-align:center;font-size:38px;font-weight:300;color:#7a7a7a}
  .social{position:absolute;top:125px;left:121px;display:flex;gap:4px}
  .social span{width:19px;height:19px;border-radius:50%;background:#cfcfcf}
  .contact{position:absolute;left:14px;bottom:16px;color:var(--white);font-size:6px;line-height:2}
  .contact .url{font-weight:700}
</style>
</head>
<body>

<section class="slide col-a row-1">
  <div class="corner"></div>
  <div class="cover-wedge"></div>
  <div class="band"></div>
  <div class="mark mark-cover"><span class="name">MERIDIAN</span><span class="sub">NEUROLAB</span></div>
</section>

<section class="slide col-b row-1">
  <div class="corner"></div>
  <div class="cover-wedge"></div>
  <div class="band"></div>
  <div class="title-block">
    <p class="kicker">COMPANY PRESENTATION</p>
    <h1>TITLE HERE</h1>
    <h2>Presentation Subtitle</h2>
  </div>
  <div class="mark mark-small"><span class="name">MERIDIAN</span><span class="sub">NEUROLAB</span></div>
</section>

<section class="slide col-a row-2">
  <div class="agenda-rail"></div>
  <div class="aqua-wedge"></div>
  <div class="agenda">
    <h3>TODAY’S AGENDA</h3>
    <h4>TOPIC TITLE</h4>
    <div class="agenda-item">Topic Subtitle<span class="leader"></span><span class="ref">#</span></div>
    <div class="agenda-item">Topic Subtitle<span class="leader"></span><span class="ref">#</span></div>
    <div class="agenda-item">Topic Subtitle<span class="leader"></span><span class="ref">#</span></div>
    <h4>TOPIC TITLE</h4>
    <div class="agenda-item">Topic Subtitle<span class="leader"></span><span class="ref">#</span></div>
    <div class="agenda-item">Topic Subtitle<span class="leader"></span><span class="ref">#</span></div>
    <h4>TOPIC TITLE</h4>
    <div class="agenda-item">Topic Subtitle<span class="leader"></span><span class="ref">#</span></div>
    <div class="agenda-item">Topic Subtitle<span class="leader"></span><span class="ref">#</span></div>
    <div class="agenda-item">Topic Subtitle<span class="leader"></span><span class="ref">#</span></div>
  </div>
  <footer class="footer">
    <span class="footer-text deck-title">PRESENTATION TITLE</span>
    <span class="footer-text deck-sub">Presentation Subtitle</span>
    <div class="mark mark-small"><span class="name">MERIDIAN</span><span class="sub">NEUROLAB</span></div>
  </footer>
</section>

<section class="slide col-b row-2">
  <div class="corner"></div>
  <div class="aqua-wedge"></div>
  <p class="label company-title">COMPANY NAME</p>
  <p class="fine company-intro">Short overview of the company and its clinical services, written in two or three calm lines for the reader.</p>
  <div class="bullet" style="top:92px"><p class="fine">Key point about the service, kept brief and clear for the audience.</p></div>
  <div class="bullet" style="top:121px"><p class="fine">Key point about the service, kept brief and clear for the audience.</p></div>
  <div class="bullet" style="top:150px"><p class="fine">Key point about the service, kept brief and clear for the audience.</p></div>
  <div class="bullet" style="top:178px"><p class="fine">Key point about the service, kept brief and clear for the audience.</p></div>
  <div class="placeholder" role="img" aria-label="Company photo" style="left:196px;top:22px;width:135px;height:188px">
    <svg width="52" height="46" viewBox="0 0 52 46"><rect x="1" y="1" width="50" height="44" fill="none" stroke="#fff" stroke-width="2"/><circle cx="18" cy="15" r="4" fill="#fff"/><path d="M8 37 L22 22 L30 30 L36 24 L45 37 Z" fill="#fff"/></svg>
  </div>
  <footer class="footer">
    <span class="footer-text page-no">1</span>
    <span class="footer-text deck-title">PRESENTATION TITLE</span>
    <span class="footer-text deck-sub">Presentation Subtitle</span>
    <div class="mark mark-small"><span class="name">MERIDIAN</span><span class="sub">NEUROLAB</span></div>
  </footer>
</section>

<section class="slide col-a row-3">
  <div class="corner"></div>
  <div class="aqua-wedge"></div>
  <div class="member" style="left:13px">
    <div class="avatar placeholder" role="img" aria-label="Team member portrait"><svg width="28" height="25" viewBox="0 0 52 46"><rect x="1" y="1" width="50" height="44" fill="none" stroke="#fff" stroke-width="3"/><circle cx="18" cy="15" r="4" fill="#fff"/><path d="M8 37 L22 22 L30 30 L36 24 L45 37 Z" fill="#fff"/></svg></div>
    <p class="label">NAME HERE</p><p class="role">Job title</p>
    <p class="fine">Short bio line about this person, their role and experience in the team.</p>
  </div>
  <div class="member" style="left:125px">
    <div class="avatar placeholder" role="img" aria-label="Team member portrait"><svg width="28" height="25" viewBox="0 0 52 46"><rect x="1" y="1" width="50" height="44" fill="none" stroke="#fff" stroke-width="3"/><circle cx="18" cy="15" r="4" fill="#fff"/><path d="M8 37 L22 22 L30 30 L36 24 L45 37 Z" fill="#fff"/></svg></div>
    <p class="label">NAME HERE</p><p class="role">Job title</p>
    <p class="fine">Short bio line about this person, their role and experience in the team.</p>
  </div>
  <div class="member" style="left:236px">
    <div class="avatar placeholder" role="img" aria-label="Team member portrait"><svg width="28" height="25" viewBox="0 0 52 46"><rect x="1" y="1" width="50" height="44" fill="none" stroke="#fff" stroke-width="3"/><circle cx="18" cy="15" r="4" fill="#fff"/><path d="M8 37 L22 22 L30 30 L36 24 L45 37 Z" fill="#fff"/></svg></div>
    <p class="label">NAME HERE</p><p class="role">Job title</p>
    <p class="fine">Short bio line about this person, their role and experience in the team.</p>
  </div>
  <footer class="footer">
    <span class="footer-text page-no">2</span>
    <span class="footer-text deck-title">PRESENTATION TITLE</span>
    <span class="footer-text deck-sub">Presentation Subtitle</span>
    <div class="mark mark-small"><span class="name">MERIDIAN</span><span class="sub">NEUROLAB</span></div>
  </footer>
</section>

<section class="slide col-b row-3">
  <div class="corner"></div>
  <div class="aqua-wedge"></div>
  <div class="placeholder" role="img" aria-label="Featured profile photo" style="left:25px;top:28px;width:138px;height:80px">
    <svg width="26" height="23" viewBox="0 0 52 46"><rect x="1" y="1" width="50" height="44" fill="none" stroke="#fff" stroke-width="3"/><circle cx="18" cy="15" r="4" fill="#fff"/><path d="M8 37 L22 22 L30 30 L36 24 L45 37 Z" fill="#fff"/></svg>
  </div>
  <p class="label" style="position:absolute;left:196px;top:28px">NAME HERE</p>
  <p class="fine" style="position:absolute;left:196px;top:39px;width:134px">A longer profile paragraph describing this person, their background, areas of expertise and the work they lead within the team. It gives context for the audience and closes with a note on current projects.</p>
  <div class="divider"></div>
  <div class="placeholder" role="img" aria-label="Profile photo" style="left:25px;top:150px;width:53px;height:35px">
    <svg width="18" height="16" viewBox="0 0 52 46"><rect x="1" y="1" width="50" height="44" fill="none" stroke="#fff" stroke-width="3"/><circle cx="18" cy="15" r="4" fill="#fff"/><path d="M8 37 L22 22 L30 30 L36 24 L45 37 Z" fill="#fff"/></svg>
  </div>
  <div style="position:absolute;left:87px;top:150px;width:80px">
    <p class="label">NAME HERE</p><p class="role">Job title</p>
    <p class="fine">Short bio line about this person and their role in the team.</p>
  </div>
  <div class="placeholder" role="img" aria-label="Profile photo" style="left:198px;top:150px;width:52px;height:35px">
    <svg width="18" height="16" viewBox="0 0 52 46"><rect x="1" y="1" width="50" height="44" fill="none" stroke="#fff" stroke-width="3"/><circle cx="18" cy="15" r="4" fill="#fff"/><path d="M8 37 L22 22 L30 30 L36 24 L45 37 Z" fill="#fff"/></svg>
  </div>
  <div style="position:absolute;left:260px;top:150px;width:74px">
    <p class="label">NAME HERE</p><p class="role">Job title</p>
    <p class="fine">Short bio line about this person and their role in the team.</p>
  </div>
  <footer class="footer">
    <span class="footer-text page-no">3</span>
    <span class="footer-text deck-title">PRESENTATION TITLE</span>
    <span class="footer-text deck-sub">Presentation Subtitle</span>
    <div class="mark mark-small"><span class="name">MERIDIAN</span><span class="sub">NEUROLAB</span></div>
  </footer>
</section>

<section class="slide col-a row-4">
  <div class="corner"></div>
  <div class="aqua-wedge"></div>
  <svg class="donut" width="160" height="160" viewBox="0 0 160 160" style="position:absolute;left:18px;top:33px">
    <g transform="rotate(-90 80 80)" fill="none" stroke-width="36">
      <circle cx="80" cy="80" r="55" stroke="var(--series-1)" stroke-dasharray="199.4 345.6" stroke-dashoffset="0"/>
      <circle cx="80" cy="80" r="55" stroke="var(--series-2)" stroke-dasharray="83.5 345.6" stroke-dashoffset="-199.4"/>
      <circle cx="80" cy="80" r="55" stroke="var(--series-3)" stroke-dasharray="32.9 345.6" stroke-dashoffset="-282.9"/>
      <circle cx="80" cy="80" r="55" stroke="var(--series-4)" stroke-dasharray="29.8 345.6" stroke-dashoffset="-315.8"/>
    </g>
    <circle cx="80" cy="80" r="73" fill="none" stroke="#fff" stroke-width="1.5"/>
  </svg>
  <div class="legend" style="top:35px"><p class="series"><i style="background:var(--series-1)"></i>Serie 1</p><p class="fine">Brief note explaining this data series and what it shows.</p></div>
  <div class="legend" style="top:76px"><p class="series"><i style="background:var(--series-2)"></i>Serie 1</p><p class="fine">Brief note explaining this data series and what it shows.</p></div>
  <div class="legend" style="top:117px"><p class="series"><i style="background:var(--series-3)"></i>Serie 1</p><p class="fine">Brief note explaining this data series and what it shows.</p></div>
  <div class="legend" style="top:158px"><p class="series"><i style="background:var(--series-4)"></i>Serie 1</p><p class="fine">Brief note explaining this data series and what it shows.</p></div>
  <footer class="footer">
    <span class="footer-text page-no">4</span>
    <span class="footer-text deck-title">PRESENTATION TITLE</span>
    <span class="footer-text deck-sub">Presentation Subtitle</span>
    <div class="mark mark-small"><span class="name">MERIDIAN</span><span class="sub">NEUROLAB</span></div>
  </footer>
</section>

<section class="slide col-b row-4">
  <div class="corner"></div>
  <div class="cover-wedge"></div>
  <div class="band"></div>
  <p class="thanks">Thanks</p>
  <div class="social" aria-label="Social channels"><span></span><span></span><span></span><span></span><span></span></div>
  <div class="contact">
    <p class="url">http://meridianneurolab.net/</p>
    <p>admin@meridianneurolab.com</p>
    <p>1480 Lakeshore Avenue, Cedar Bend, TX 75410</p>
  </div>
  <div class="mark mark-small"><span class="name">MERIDIAN</span><span class="sub">NEUROLAB</span></div>
</section>

</body>
</html>
```